Construction company stationary design

We're wanting to develop a new professional stationary set for a newly establised property related business using our existing logo (attached). Business incorporates renovations, property investment and property development.

Specifically needing letter head, business cards, envelopes, email signature and need to get tshirt and caps embroydered.

Looking for something quite modern but professional using white, black and green.

Investment

```html
<!DOCTYPE html>
<html lang="en">
<head>
<meta charset="utf-8">
<title>KTR Builders – Envelope</title>
<link rel="stylesheet" href="https://fonts.googleapis.com/css2?family=Source+Sans+3:wght@400;700&display=swap">
<style>
  :root {
    --brand-green: #7cc242;
    --ink: #1e1e1e;
    --rule: #2a2a2a;
    --paper-top: #ffffff;
    --paper-bottom: #eeeeee;
    --art-dark: #1a1a1a;
  }
  html, body {
    margin: 0;
    padding: 0;
    overflow: hidden;
    background: #ffffff;
  }
  .envelope {
    position: relative;
    width: 1200px;
    height: 601px;
    overflow: hidden;
    background: linear-gradient(to bottom, var(--paper-top) 0%, var(--paper-top) 28%, var(--paper-bottom) 100%);
    font-family: "Source Sans 3", Arial, sans-serif;
    color: var(--ink);
  }
  .brand-name {
    position: absolute;
    left: 82px;
    top: 210px;
    margin: 0;
    font-size: 40px;
    font-weight: 700;
    line-height: 1;
    letter-spacing: -0.5px;
    color: var(--brand-green);
    text-transform: uppercase;
  }
  .field {
    position: absolute;
    display: flex;
    align-items: baseline;
    font-size: 19px;
    line-height: 1;
    white-space: nowrap;
  }
  .field-label {
    padding-right: 4px;
  }
  .field-line {
    flex: 1;
    border-bottom: 1.5px solid var(--rule);
    transform: translateY(2px);
  }
  .recipient .field { left: 86px; width: 356px; }
  .recipient .street { top: 348px; }
  .recipient .city { top: 373px; }
  .recipient .postal { top: 398px; }
  .recipient .state { top: 423px; }

  .sender .address { left: 86px; top: 532px; width: 338px; }
  .sender .phone { left: 424px; top: 532px; width: 352px; }
  .sender .email { left: 86px; top: 556px; width: 348px; }
  .sender .web { left: 434px; top: 556px; width: 350px; }

  .skyline-art {
    position: absolute;
    left: 912px;
    top: 346px;
    width: 252px;
    height: 255px;
    background: linear-gradient(to right, var(--brand-green) 0%, var(--brand-green) 45%, var(--art-dark) 100%);
    opacity: 0.85;
  }
</style>
</head>
<body>
  <div class="envelope">
    <h1 class="brand-name">KTR Builders</h1>

    <div class="recipient">
      <div class="field street"><span class="field-label">Street no.</span><span class="field-line"></span></div>
      <div class="field city"><span class="field-label">City</span><span class="field-line"></span></div>
      <div class="field postal"><span class="field-label">Postal Code</span><span class="field-line"></span></div>
      <div class="field state"><span class="field-label">State</span><span class="field-line"></span></div>
    </div>

    <div class="sender">
      <div class="field address"><span class="field-label">Address</span><span class="field-line"></span></div>
      <div class="field phone"><span class="field-label">Phone Number</span><span class="field-line"></span></div>
      <div class="field email"><span class="field-label">Email</span><span class="field-line"></span></div>
      <div class="field web"><span class="field-label">Web address</span><span class="field-line"></span></div>
    </div>

    <div class="skyline-art" role="img" aria-label="Outline illustration of green and black tower buildings rising from the bottom edge"></div>
  </div>
</body>
</html>
```